School Poster and Prompt Design

I would like posters created for each of our school values (from the attached Way of Working document). In these posters I would like our logo, and some graphics or pictures - you can use the strategic plan attached for some examples.

I would also like a Code of Conduct Prompt for teachers and students (smaller design that can be used as a sticker for a laptop) based on the attached Tallowmere Heights Basics document. I have also attached a photo example, which we quite like that can be used for a base. This document is called example classroom management prompts.

Target Market(s)

School and students

Requirements
Must have
• Logo built into the design
Our school motto at the bottom 'Strive to Accomplish'
Design that incorporates elements that relate to each of the values.
Design that looks and feels like the example. In our school colours.
Nice to have
• Posters - Easy to read and understand from a distance.
Prompt - Easy to read and understand if turned into a sticker for a laptop.

```html
<!DOCTYPE html>
<html lang="en">
<head>
<meta charset="utf-8">
<title>Classroom Routines – Tallowmere Heights High School</title>
<link href="https://fonts.googleapis.com/css2?family=Arimo:wght@400;700&display=swap" rel="stylesheet">
<style>
  :root {
    --navy: #161640;
    --navy-deep: #10123a;
    --royal: #0b4f8f;
    --royal-mid: #1560a6;
    --sky: #27b9ec;
    --sky-soft: #45c6f0;
    --ink-blue: #1c4f9c;
    --link-blue: #2a8fd0;
    --white: #ffffff;
    --paper: #ffffff;
  }
  * { box-sizing: border-box; margin: 0; padding: 0; }
  html, body { width: 1019px; height: 1200px; overflow: hidden; background: var(--paper); }
  body { font-family: "Arimo", Arial, sans-serif; color: var(--ink-blue); }
  .poster { position: relative; width: 1019px; height: 1200px; background: var(--paper); }

  /* Header */
  .masthead {
    position: absolute; left: 0; top: 20px; width: 1019px; height: 170px;
    background: linear-gradient(90deg, var(--royal-mid) 0%, var(--navy) 55%, var(--navy-deep) 100%);
  }
  .school-mark {
    position: absolute; left: 40px; top: 0; width: 220px; height: 170px;
    display: flex; align-items: center; gap: 12px;
  }
  .school-mark .dot {
    flex: none; width: 34px; height: 34px; border-radius: 50%; background: var(--sky);
  }
  .school-mark .name {
    color: var(--white); font-weight: 700; font-size: 20px; line-height: 1.2; letter-spacing: .5px;
  }
  .masthead .title {
    position: absolute; left: 280px; width: 460px; top: 50px; text-align: center;
    color: var(--white); font-size: 36px; letter-spacing: 1.5px; font-weight: 400;
  }
  .masthead .subtitle {
    position: absolute; left: 280px; width: 460px; top: 103px; text-align: center;
    color: var(--sky); font-size: 20px; letter-spacing: .3px;
  }
  .masthead .student-photo {
    position: absolute; right: 0; top: 0; width: 270px; height: 170px;
    background: linear-gradient(90deg, rgba(16,18,58,0) 0%, #3a5f86 45%, #6f93b5 75%, #2c4563 100%);
  }

  .values {
    position: absolute; top: 207px; left: 0; width: 1019px; text-align: center;
    color: var(--link-blue); font-size: 18px; letter-spacing: .4px; word-spacing: 2px;
  }
  .values .sep { margin: 0 14px; }

  /* Entry */
  .entry {
    position: absolute; left: 33px; top: 241px; width: 953px; height: 237px;
    background: linear-gradient(180deg, var(--sky) 0%, var(--sky) 35%, var(--royal) 100%);
    border-radius: 4px;
  }
  .entry .notch { position: absolute; left: 450px; top: 0; }
  .entry h2 {
    text-align: center; color: var(--white); font-size: 52px; font-weight: 700;
    letter-spacing: 2px; margin-top: 20px;
  }
  .entry-card {
    position: absolute; top: 80px; width: 279px; height: 140px; color: var(--white);
    padding: 34px 0 0 31px; border-radius: 2px;
  }
  .entry-card.light { background: var(--sky); }
  .entry-card.dark { background: var(--royal); }
  .entry-card h3 { font-size: 17px; font-weight: 700; letter-spacing: .8px; margin-bottom: 10px; }
  .entry-card ul { list-style: none; font-size: 13.5px; line-height: 18px; }
  .entry-card li::before { content: "•"; margin-right: 9px; font-size: 10px; }

  /* Start of lesson */
  .lesson {
    position: absolute; left: 33px; top: 500px; width: 953px; height: 212px;
    border: 3px dotted var(--link-blue);
  }
  .lesson h2 {
    position: absolute; top: 30px; left: 0; width: 100%; text-align: center; padding-left: 0;
    color: var(--royal); font-size: 44px; font-weight: 700; letter-spacing: 1.5px;
  }
  .lesson .lead {
    position: absolute; top: 90px; left: 0; width: 100%; text-align: center;
    color: var(--link-blue); font-size: 17px; letter-spacing: .3px;
  }
  .attendance-note {
    position: absolute; left: -14px; top: 25px; width: 132px; height: 132px; border-radius: 50%;
    background: linear-gradient(180deg, var(--royal-mid), var(--sky));
    border: 3px solid var(--sky);
    color: var(--white); font-size: 11px; font-weight: 700; line-height: 13.5px;
    display: flex; align-items: center; justify-content: center; text-align: center; padding: 0 14px;
  }
  .check-row { position: absolute; left: 0; width: 100%; display: flex; }
  .check-item { flex: 1; text-align: center; font-size: 17px; letter-spacing: .3px; }
  .check-item svg { display: block; margin: 0 auto 10px; }
  .lesson .check-row { top: 135px; padding: 0 20px 0 70px; color: var(--royal); }

  /* Exit */
  .exit {
    position: absolute; left: 0; top: 743px; width: 1019px; height: 235px; background: var(--navy);
  }
  .exit h2 {
    text-align: center; color: var(--white); font-size: 52px; font-weight: 700; letter-spacing: 2px;
    margin-top: 20px;
  }
  .exit .lead {
    text-align: center; color: var(--sky); font-size: 20px; letter-spacing: .3px; margin-top: 6px;
  }
  .exit .check-row { top: 133px; padding: 0 60px; color: var(--white); }
  .exit .check-item { font-size: 14px; line-height: 17px; }
  .exit .check-item .label { height: 34px; display: flex; align-items: center; justify-content: center; }
  .exit .pointer { position: absolute; left: 490px; bottom: -18px; }

  /* Recognition */
  .recognise-band {
    position: absolute; left: 0; top: 1008px; width: 1019px; height: 44px;
    background: linear-gradient(90deg, var(--sky) 0%, var(--royal-mid) 70%, var(--royal) 100%);
    color: var(--white); font-size: 19px; letter-spacing: .4px;
    display: flex; align-items: center; justify-content: center;
  }
  .rewards { position: absolute; left: 0; top: 1068px; width: 1019px; display: flex; padding: 0 50px; }
  .reward { flex: 1; text-align: center; color: var(--ink-blue); font-size: 18px; line-height: 21px; }
  .reward svg { display: block; margin: 0 auto 12px; }
</style>
</head>
<body>
<main class="poster">

  <header class="masthead">
    <div class="school-mark">
      <span class="dot"></span>
      <span class="name">Tallowmere Heights High School</span>
    </div>
    <h1 class="title">CLASSROOM ROUTINES</h1>
    <p class="subtitle">WAY OF WORKING</p>
    <div class="student-photo" role="img" aria-label="Photo of a smiling student in school uniform"></div>
  </header>

  <p class="values">RESPECT<span class="sep">•</span>INDUSTRY<span class="sep">•</span>COOPERATION</p>

  <section class="entry">
    <svg class="notch" width="52" height="16" viewBox="0 0 52 16" aria-hidden="true"><polygon points="0,0 52,0 26,16" fill="#ffffff"/></svg>
    <h2>ENTRY</h2>
    <div class="entry-card light" style="left:26px;">
      <h3>COMMITMENT</h3>
      <ul><li>On time</li><li>Correct uniform</li><li>Ready to learning</li></ul>
    </div>
    <div class="entry-card dark" style="left:337px;">
      <h3>COURTESY</h3>
      <ul><li>In line</li><li>Waiting quietly</li><li>Stand behind chairs</li></ul>
    </div>
    <div class="entry-card light" style="left:648px; padding-left:70px;">
      <h3>COOPERATION</h3>
      <ul><li>In the right seat</li><li>Ready to participate</li><li>Actively listening</li></ul>
    </div>
  </section>

  <section class="lesson">
    <div class="attendance-note">Mark ID Attend in the first 15 minutes and confirm with head count</div>
    <h2>START OF LESSON</h2>
    <p class="lead">SHOW AND EXPLAIN TO STUDENTS</p>
    <div class="check-row">
      <div class="check-item">
        <svg width="34" height="28" viewBox="0 0 34 28" aria-hidden="true"><circle cx="14" cy="15" r="11" fill="none" stroke="#2a8fd0" stroke-width="1.8"/><path d="M8 14 l6 7 L32 2" fill="none" stroke="#2a8fd0" stroke-width="2.6"/></svg>
        LESSON INTENTION
      </div>
      <div class="check-item">
        <svg width="34" height="28" viewBox="0 0 34 28" aria-hidden="true"><circle cx="14" cy="15" r="11" fill="none" stroke="#2a8fd0" stroke-width="1.8"/><path d="M8 14 l6 7 L32 2" fill="none" stroke="#2a8fd0" stroke-width="2.6"/></svg>
        SUCCESS CRITERIA
      </div>
      <div class="check-item">
        <svg width="34" height="28" viewBox="0 0 34 28" aria-hidden="true"><circle cx="14" cy="15" r="11" fill="none" stroke="#2a8fd0" stroke-width="1.8"/><path d="M8 14 l6 7 L32 2" fill="none" stroke="#2a8fd0" stroke-width="2.6"/></svg>
        WAY OF WORKING FOCUS
      </div>
    </div>
  </section>

  <section class="exit">
    <h2>EXIT</h2>
    <p class="lead">EXIT STRATEGY USED TO CHECK FOR UNDERSTANDING</p>
    <div class="check-row">
      <div class="check-item">
        <svg width="34" height="28" viewBox="0 0 34 28" aria-hidden="true"><circle cx="14" cy="15" r="11" fill="none" stroke="#27b9ec" stroke-width="1.8"/><path d="M8 14 l6 7 L32 2" fill="none" stroke="#27b9ec" stroke-width="2.6"/></svg>
        <div class="label">IT IS CHECKED</div>
      </div>
      <div class="check-item">
        <svg width="34" height="28" viewBox="0 0 34 28" aria-hidden="true"><circle cx="14" cy="15" r="11" fill="none" stroke="#27b9ec" stroke-width="1.8"/><path d="M8 14 l6 7 L32 2" fill="none" stroke="#27b9ec" stroke-width="2.6"/></svg>
        <div class="label">ENVIRONMENT LEFT<br>NEAT AND TIDY</div>
      </div>
      <div class="check-item">
        <svg width="34" height="28" viewBox="0 0 34 28" aria-hidden="true"><circle cx="14" cy="15" r="11" fill="none" stroke="#27b9ec" stroke-width="1.8"/><path d="M8 14 l6 7 L32 2" fill="none" stroke="#27b9ec" stroke-width="2.6"/></svg>
        <div class="label">DOORS AND<br>WINDOWS LOCKED</div>
      </div>
    </div>
    <svg class="pointer" width="40" height="18" viewBox="0 0 40 18" aria-hidden="true"><polygon points="0,0 40,0 20,18" fill="#161640"/></svg>
  </section>

  <div class="recognise-band">RECOGNISE POSITIVE BEHAVIOUR BY:</div>

  <section class="rewards">
    <div class="reward">
      <svg width="60" height="62" viewBox="0 0 60 62" aria-hidden="true">
        <polygon points="30,4 4,28 11,28 11,56 49,56 49,28 56,28" fill="#161640"/>
        <polygon points="30,4 4,28 9,31 30,12 51,31 56,28" fill="#2a8fd0"/>
        <rect x="24" y="36" width="12" height="20" fill="#2a8fd0"/>
      </svg>
      Assigning house points
    </div>
    <div class="reward">
      <svg width="60" height="62" viewBox="0 0 60 62" aria-hidden="true">
        <rect x="14" y="2" width="32" height="36" fill="#2a8fd0"/>
        <rect x="19" y="8" width="12" height="2" fill="#ffffff"/><rect x="19" y="13" width="18" height="2" fill="#ffffff"/>
        <polygon points="4,26 30,44 56,26 56,60 4,60" fill="#161640"/>
        <polyline points="4,60 30,40 56,60" fill="none" stroke="#ffffff" stroke-width="2"/>
      </svg>
      Postcard or<br>Student of the Week
    </div>
    <div class="reward">
      <svg width="60" height="62" viewBox="0 0 60 62" aria-hidden="true">
        <path d="M10 16 q-6 6 0 20 q10 18 26 24 q8 2 12 -4 l-8 -9 q-5 4 -10 0 q-8 -8 -10 -14 q-2 -5 3 -8 l-7 -10 z" fill="#161640"/>
        <circle cx="42" cy="16" r="13" fill="#ffffff" stroke="#2a8fd0" stroke-width="3"/>
        <polygon points="42,8 34,15 36,15 36,23 48,23 48,15 50,15" fill="#161640"/>
      </svg>
      Phone call home
    </div>
  </section>

</main>
</body>
</html>
```